Business Card Design needed - Something Awesome!

Need a business card designed. Company is "Marlowe Advisory" we do consulting and also have sales automation technology.
I'm going to use thick stock or metal, something really nice... I was thinking about a QR Code on the back that would just upload my contact info to the persons contact, etc -

This is a Strategy Company with a tech feel. I'm open to ideas but really want this to be nice!

I need a template that should include:

Name | Position or Title
D: 415.902.3376
www.marloweadvisory.example

I'm going to attach my contact so you can use that one, I need to get this printed.

Target Market(s)

Small to mid size customers, Entrepreneurs etc.

Industry/Entity Type

Consulting, Tech, Private Equity.

Contact Information for Business Card

Name, Phone, Maybe email, URL

Font styles to use
Sans Serif

Colors

Designer to choose only greyscale colors for use in the design.

Requirements
Must have
• Fresh, Clean, stand out from the crowd - will be on thick stock or metal.
Nice to have
• Clean, simple yet impactful.
Should not have
• Not cartoonish

```html
<!DOCTYPE html>
<html lang="en">
<head>
<meta charset="utf-8">
<title>Marlowe Advisory – Business Card</title>
<link rel="stylesheet" href="https://fonts.googleapis.com/css2?family=Arimo:wght@400;700&display=swap">
<style>
  :root {
    --backdrop: #3a3a3a;
    --card: #111111;
    --card-edge: #000000;
    --silver: #d6d6d6;
    --silver-soft: #a9a9a9;
    --rule: #5a5a5a;
    --pattern-dark: #0b0b0b;
    --pattern-mid: #2c2c2c;
  }
  * { box-sizing: border-box; margin: 0; padding: 0; }
  html, body {
    width: 1200px; height: 801px; overflow: hidden;
    background: var(--backdrop);
    font-family: "Arimo", Arial, sans-serif;
  }
  .sheet {
    position: relative; width: 1200px; height: 801px;
    display: flex; align-items: center; justify-content: center; gap: 40px;
  }
  .card {
    width: 520px; height: 297px; background: var(--card);
    border: 1px solid var(--card-edge); position: relative;
    box-shadow: 0 10px 30px rgba(0,0,0,.35);
  }
  /* Front */
  .card-front { display: flex; align-items: center; }
  .wordmark {
    flex: none; width: 258px; padding-left: 30px;
    color: var(--silver); font-size: 36px; font-weight: 400;
    letter-spacing: 1px; white-space: nowrap;
  }
  .divider { flex: none; width: 1px; height: 120px; background: var(--rule); }
  .details { flex: none; padding-left: 22px; color: var(--silver); white-space: nowrap; }
  .details .name { font-size: 16px; font-weight: 700; letter-spacing: .5px; }
  .details .title { font-size: 13px; color: var(--silver-soft); margin-top: 4px; }
  .contact-list { list-style: none; margin-top: 16px; }
  .contact-list li {
    display: flex; align-items: center; gap: 8px;
    font-size: 12.5px; color: var(--silver); line-height: 1.5;
  }
  .contact-list svg { width: 11px; height: 11px; fill: var(--silver); flex: none; }
  /* Back */
  .card-back { overflow: hidden; }
  .pattern-field {
    position: absolute; inset: 0;
    background: linear-gradient(120deg, var(--pattern-dark) 0%, var(--pattern-mid) 100%);
  }
  .back-name {
    position: absolute; inset: 0; display: flex; align-items: center; justify-content: center;
    color: var(--silver); font-size: 22px; font-weight: 400; letter-spacing: 1px;
  }
</style>
</head>
<body>
<main class="sheet">
  <section class="card card-front" aria-label="Card front">
    <div class="wordmark">MARLOWE</div>
    <div class="divider"></div>
    <div class="details">
      <p class="name">ADRIAN K. HOLLOWAY</p>
      <p class="title">Founder / CEO</p>
      <ul class="contact-list">
        <li>
          <svg viewBox="0 0 24 24" aria-hidden="true"><path d="M6.6 10.8a15 15 0 0 0 6.6 6.6l2.2-2.2a1 1 0 0 1 1-.25 11.4 11.4 0 0 0 3.6.57 1 1 0 0 1 1 1V20a1 1 0 0 1-1 1A17 17 0 0 1 3 4a1 1 0 0 1 1-1h3.5a1 1 0 0 1 1 1c0 1.25.2 2.45.57 3.6a1 1 0 0 1-.25 1z"/></svg>
          415.902.3376
        </li>
        <li>
          <svg viewBox="0 0 24 24" aria-hidden="true"><path d="M2 5h20v14H2z M2 5l10 8 10-8" fill="none" stroke="#d6d6d6" stroke-width="2"/></svg>
          info@marloweadvisory.example
        </li>
        <li>
          <svg viewBox="0 0 24 24" aria-hidden="true"><circle cx="12" cy="12" r="9" fill="none" stroke="#d6d6d6" stroke-width="2"/><path d="M3 12h18M12 3c3 3 3 15 0 18M12 3c-3 3-3 15 0 18" fill="none" stroke="#d6d6d6" stroke-width="1.6"/></svg>
          www.marloweadvisory.example
        </li>
      </ul>
    </div>
  </section>
  <section class="card card-back" aria-label="Card back">
    <div class="pattern-field" role="img" aria-label="Tonal pattern of glossy black and charcoal squares in diagonal rows"></div>
    <div class="back-name">MARLOWE</div>
  </section>
</main>
</body>
</html>
```